Cat-products company needs smart, yet endearing, business card

We need a business card design for a new, but up-and-running, business based in Honolulu, Hawaii. The business is Purrnest Nook Co. Our first product is the most environmentally-friendly cat grass kit ever seen on the planet. Future products, currently in the R&D phase, will include a variety of exciting cat scratchers. We also do consulting work to help apartment-dwellers make their home more cat-friendly and, in the future, plan on doing full, custom installs of structure to create high walkways for cats.

Target Market(s)

Middle-aged, apartment-dwelling, middle-class workers who own 1 or more cats and who dote on them.

Industry/Entity Type

Pet Care

Contact Information for Business Card

A striking, professional, yet warm and friendly design is what we're after.

Font styles to use
Serif
Sans Serif
Other font styles liked:
• Comfortaa

Colors

Designer to choose colors to be used in the design.

Requirements
Must have
• The company logo: (see attachment)
• The company name: Purrnest Nook Co
• The web address: www.purrnestnookco.com
• Email: support@purrnestnookco.com
• Phone: +1 (808) 571 6023
• Update (Fri Jun 30 3017 7:45pm Hawaii Time) I would like, is possible, uploaded picture of the cat grass kit on the back of the card with some text along the lines of: Purrnest Nook Co - Maker Of The Leafiest Feline Sprout Set Yet
Nice to have
• A cat picture, cartoon, real or silhouette that illustrates cats in action and/or relaxing; ie using the apartment space to live, play and relax in and being well-contented.
• Most of the website is done in the font: Comfortaa. It might be nice to continue using this for brand consistency.
Should not have
• Hard-to-read fonts.

```html
<!DOCTYPE html>
<html lang="en">
<head>
<meta charset="utf-8">
<title>Purrnest Nook Co — Business Card</title>
<link rel="stylesheet" href="https://fonts.googleapis.com/css2?family=Comfortaa:wght@400;700&family=Quicksand:wght@500;600&display=swap">
<style>
  :root {
    --cocoa: #5a3329;
    --cocoa-deep: #4c2a22;
    --honey: #f5b417;
    --paper: #ffffff;
    --ink: #4a2c24;
    --stage: #2b2b2b;
  }
  * { box-sizing: border-box; margin: 0; padding: 0; }
  html, body { width: 1200px; height: 1000px; overflow: hidden; }
  body {
    background: var(--stage);
    font-family: "Quicksand", "Comfortaa", sans-serif;
    position: relative;
  }
  .card {
    position: absolute;
    left: 260px;
    width: 680px;
    height: 390px;
    border-radius: 4px;
    overflow: hidden;
    box-shadow: 0 14px 30px rgba(0,0,0,.45);
  }
  .card--front { top: 60px; background: var(--cocoa); }
  .card--back { top: 530px; background: var(--paper); }

  .front-brand {
    position: absolute; inset: 0;
    display: flex; align-items: center; justify-content: center; gap: 18px;
  }
  .brand-mark {
    width: 46px; height: 46px; background: var(--paper); border-radius: 4px;
  }
  .brand-name {
    font-family: "Comfortaa", sans-serif; font-weight: 700;
    color: var(--honey); font-size: 44px; letter-spacing: .5px;
  }

  .back-art { position: absolute; inset: 0; }
  .back-brand {
    position: absolute; left: 40px; top: 44px;
    font-family: "Comfortaa", sans-serif; font-weight: 700;
    color: var(--honey); font-size: 32px;
  }
  .holder { position: absolute; left: 52px; top: 118px; }
  .holder-name { color: var(--honey); font-size: 26px; font-weight: 600; }
  .holder-role { color: var(--ink); font-size: 16px; font-weight: 500; margin-top: 2px; }
  .address {
    position: absolute; left: 62px; top: 196px;
    color: var(--ink); font-size: 13px; line-height: 1.45;
  }
  .contacts {
    position: absolute; left: 28px; top: 286px;
    list-style: none; color: var(--paper); font-size: 13px; line-height: 1.9;
  }
  .contacts li { display: flex; align-items: center; gap: 12px; }
  .contacts svg { width: 13px; height: 13px; fill: var(--honey); }
  .contacts .accent { color: var(--honey); }
</style>
</head>
<body>

<section class="card card--front" aria-label="Business card front">
  <div class="front-brand">
    <span class="brand-mark"></span>
    <span class="brand-name">Purrnest Nook Co</span>
  </div>
</section>

<section class="card card--back" aria-label="Business card back">
  <svg class="back-art" viewBox="0 0 680 390" width="680" height="390" aria-hidden="true">
    <polygon fill="var(--cocoa)" points="0,270 440,270 440,200 680,130 680,390 0,390"/>
    <rect x="478" y="150" width="110" height="110" fill="var(--cocoa)" stroke="var(--paper)" stroke-width="6"/>
  </svg>

  <div class="back-brand">Purrnest Nook Co</div>

  <div class="holder">
    <div class="holder-name">Lena Moriyama</div>
    <div class="holder-role">Director</div>
  </div>

  <address class="address" style="font-style:normal">
    Your Street Address,<br>Country,1234
  </address>

  <ul class="contacts">
    <li>
      <svg viewBox="0 0 16 16"><path d="M4 1l3 3-2 2c1 2 3 4 5 5l2-2 3 3-2 3C7 15 1 9 1 3z"/></svg>
      +1 (808) 571 6023
    </li>
    <li>
      <svg viewBox="0 0 16 16"><path d="M1 3h14v10H1z M1 3l7 6 7-6" stroke="var(--cocoa)" stroke-width="1"/></svg>
      support@purrnestnookco.com
    </li>
    <li>
      <svg viewBox="0 0 16 16"><circle cx="8" cy="8" r="7"/></svg>
      <span>www.<span class="accent">purrnestnookco</span>.com</span>
    </li>
  </ul>
</section>

</body>
</html>
```